Local Roofing Company Billboard Design

We need a billboard design for an 8' x 32' billboard. This billboard would need to be easily readable and stand out well.
I have uploaded a design that we like - simple, readable, and gets the point across. We do NOT want the $1000 off offer included.
We are looking for a black background with white copy so it will stand out. We want the following on the billboard:
Brindlewick Roofing logo
brindlewick-roofing.example (optional)
555.214.7730 (mandatory)
Photo is optional, depends on how it all lays out
Production file must comply with layout requirements (uploaded).
Target Market(s)
Homeowners
Font styles to use
Other font styles liked:
- match font from logo
Colors
Designer to choose colors to be used in the design.
Requirements
Must have
- Black background, white copy, logo must be large and legible. Colors used must match our logo colors.

```html
<!DOCTYPE html>
<html lang="en">
<head>
<meta charset="utf-8">
<title>Brindlewick Roofing Billboard</title>
<link rel="stylesheet" href="https://fonts.googleapis.com/css2?family=Arvo:wght@700&family=Montserrat:wght@600;700&family=Poppins:ital,wght@1,800&display=swap">
<style>
  :root {
    --board-black: #1f1f1f;
    --brand-orange: #e8581c;
    --white: #ffffff;
    --ink: #141414;
    --page-bg: #ececec;
    --sky-light: #dcd6c8;
    --sky-warm: #c8a57e;
    --roof-brown: #9a6a4a;
  }
  html, body {
    margin: 0;
    padding: 0;
    width: 1200px;
    height: 1084px;
    overflow: hidden;
    background: var(--page-bg);
  }
  .billboard {
    position: absolute;
    left: 30px;
    top: 400px;
    width: 1140px;
    height: 284px;
    box-shadow: 0 10px 30px rgba(0,0,0,0.25);
    display: block;
  }
  .board-bg { fill: var(--board-black); }
  .chevron { fill: var(--brand-orange); }
  .phone-band { fill: var(--brand-orange); }
  .web-band { fill: var(--white); }
  .cert-mark { fill: var(--white); fill-opacity: 0.85; }
  .brand-name {
    font-family: "Arvo", serif;
    font-weight: 700;
    font-size: 92px;
    fill: var(--white);
  }
  .tagline {
    font-family: "Poppins", sans-serif;
    font-style: italic;
    font-weight: 800;
    font-size: 60px;
    fill: var(--brand-orange);
  }
  .phone-number {
    font-family: "Montserrat", sans-serif;
    font-weight: 700;
    font-size: 56px;
    fill: var(--ink);
  }
  .web-address {
    font-family: "Montserrat", sans-serif;
    font-weight: 600;
    font-size: 42px;
    fill: var(--ink);
  }
  .web-suffix { fill: var(--brand-orange); }
  .icon-phone { fill: var(--ink); }
  .icon-globe { fill: none; stroke: var(--brand-orange); stroke-width: 2.5; }
</style>
</head>
<body>
<svg class="billboard" viewBox="0 0 1908 476" preserveAspectRatio="none" xmlns="http://www.w3.org/2000/svg">
  <defs>
    <linearGradient id="photoTones" x1="0" y1="0" x2="0" y2="1">
      <stop offset="0" stop-color="var(--sky-light)"/>
      <stop offset="0.55" stop-color="var(--sky-warm)"/>
      <stop offset="1" stop-color="var(--roof-brown)"/>
    </linearGradient>
  </defs>

  <rect class="board-bg" x="0" y="0" width="1908" height="476"/>

  <!-- contact bar -->
  <polygon class="web-band" points="556,406 1300,406 1300,476 598,476"/>
  <polygon class="phone-band" points="0,406 556,406 598,476 0,476"/>

  <!-- photo area -->
  <polygon class="photo-area" role="img" aria-label="Roofer in hard hat and safety harness fastening tiles on a roof at sunset" fill="url(#photoTones)" points="1316,0 1908,0 1908,476 1316,476 1196,236"/>

  <!-- orange chevron divider -->
  <polygon class="chevron" points="1276,0 1316,0 1196,236 1316,476 1276,476 1156,236"/>

  <!-- certification mark placeholder -->
  <circle class="cert-mark" cx="1810" cy="96" r="52" role="img" aria-label="Contractor certification mark"/>

  <!-- brand -->
  <text class="brand-name" x="594" y="250" text-anchor="middle">Brindlewick Roofing</text>

  <text class="tagline" x="34" y="370" textLength="1130" lengthAdjust="spacingAndGlyphs">QUALITY ROOFING YOU CAN TRUST</text>

  <!-- phone -->
  <path class="icon-phone" d="M44,426 c4,-3 8,-1 10,3 l4,8 c1,3 0,5 -2,7 l-3,2 c2,5 6,9 11,11 l2,-3 c2,-2 4,-3 7,-2 l8,4 c4,2 5,6 2,10 l-3,4 c-3,3 -7,4 -11,2 c-14,-6 -25,-17 -31,-31 c-2,-4 -1,-8 2,-11 z"/>
  <text class="phone-number" x="94" y="462" textLength="440" lengthAdjust="spacingAndGlyphs">555.214.7730</text>

  <!-- web -->
  <g class="icon-globe">
    <circle cx="636" cy="441" r="17"/>
    <ellipse cx="636" cy="441" rx="7" ry="17"/>
    <line x1="619" y1="441" x2="653" y2="441"/>
    <line x1="622" y1="432" x2="650" y2="432"/>
    <line x1="622" y1="450" x2="650" y2="450"/>
  </g>
  <text class="web-address" x="664" y="456" textLength="560" lengthAdjust="spacingAndGlyphs">brindlewick-roofing<tspan class="web-suffix">.example</tspan></text>
</svg>
</body>
</html>
```